Simple landing page for Brambles cookbook

I need a one page landingpage where customers can order the cookbook.
This is a cookbook of a collection of recipes from our deli that we used to run.
I need a landing page where customers can come and order the book. I also need it coded. I already have the domain through hostwell.
I can send the file of the book through wetransfer. It's too big to upload here. Just so you get the feel that I am looking for.
I attached a simple text as an introduction to the page. But I am open to any suggestions. I want it all to be about the experience that we are sharing the recipes with everybody and that it's for sale. The book is $29.99, shipping included.
Customers have to be able to click and buy the book from it.

Coding

Coded - Design and coding required

Number of Pages Required

1 page

Font styles to use
Sans Serif

Requirements
Must have
• Same colors as the cookbook

```html
<!DOCTYPE html>
<html lang="en">
<head>
<meta charset="utf-8">
<title>Brambles Cookbook</title>
<link rel="stylesheet" href="https://fonts.googleapis.com/css2?family=Montserrat:wght@400;500;600;700&family=Noto+Serif:wght@400;500;700&display=swap">
<style>
  :root {
    --header-bg: #f5faff;
    --brand-brown: #3b2a22;
    --sun-yellow: #f8d42e;
    --panel-yellow: rgba(252, 222, 90, 0.78);
    --ink: #111111;
    --white: #ffffff;
    --photo-dark: #3a2418;
    --photo-mid: #a8652a;
    --photo-warm: #d9923c;
  }
  * { box-sizing: border-box; margin: 0; padding: 0; }
  html, body { width: 1200px; height: 697px; overflow: hidden; }
  body { position: relative; font-family: "Noto Serif", Georgia, serif; color: var(--ink); background: var(--header-bg); }

  .site-header {
    position: absolute; top: 0; left: 0; width: 1200px; height: 51px;
    background: var(--header-bg);
    display: flex; align-items: center; justify-content: center;
  }
  .brand-name {
    font-family: "Montserrat", Arial, sans-serif; font-weight: 700;
    font-size: 30px; letter-spacing: 0.5px; color: var(--brand-brown);
  }

  .hero {
    position: absolute; top: 51px; left: 0; width: 1200px; height: 598px;
    overflow: hidden;
  }
  .hero-photo {
    position: absolute; inset: 0;
    background:
      radial-gradient(ellipse 420px 300px at 560px 300px, var(--photo-warm), transparent 70%),
      radial-gradient(ellipse 300px 220px at 80px 80px, #c9852f, transparent 75%),
      linear-gradient(180deg, #6b4024 0%, var(--photo-mid) 40%, #5a3522 75%, var(--photo-dark) 100%);
  }

  .intro-panel {
    position: absolute; left: 111px; top: 41px; width: 648px; height: 517px;
    background: var(--panel-yellow); border-radius: 6px; padding: 13px 15px;
  }
  .intro-frame {
    width: 100%; height: 100%;
    border: 1.2px dashed #4a4030; border-radius: 6px;
    padding: 4px 12px 0;
  }
  .intro-title { font-size: 34px; font-weight: 500; line-height: 1.2; }
  .intro-subtitle {
    display: inline-block; font-size: 25px; font-weight: 400; line-height: 1.3;
    padding-bottom: 6px; border-bottom: 2px solid var(--ink); margin-bottom: 10px;
  }
  .intro-text p { font-size: 14.6px; line-height: 24px; margin-bottom: 13px; }

  .offer-circle {
    position: absolute; left: 799px; top: 110px; width: 339px; height: 339px;
    border-radius: 50%; background: var(--sun-yellow);
  }
  .book-cover {
    position: absolute; left: 855px; top: 32px; width: 232px; height: 390px;
    border-radius: 3px;
    background: linear-gradient(90deg, #a9dcf3 0 7%, #dfeaf2 7% 100%);
    box-shadow: 4px 6px 14px rgba(0,0,0,0.35);
  }
  .price-block {
    position: absolute; left: 875px; top: 436px; width: 196px; text-align: center; color: var(--white);
  }
  .price-label { font-family: "Montserrat", Arial, sans-serif; font-size: 14px; }
  .price-amount { font-family: "Noto Serif", Georgia, serif; font-weight: 700; font-size: 42px; line-height: 1.2; }
  .buy-button {
    position: absolute; left: 875px; top: 522px; width: 196px; height: 55px;
    background: var(--sun-yellow); border: 2px solid #e6b34a; border-radius: 5px;
    font-family: "Montserrat", Arial, sans-serif; font-weight: 600; font-size: 17px;
    color: var(--ink); display: flex; align-items: center; justify-content: center;
    text-decoration: none;
  }

  .site-footer {
    position: absolute; left: 0; top: 649px; width: 1200px; height: 48px;
    background: var(--sun-yellow);
    font-family: "Montserrat", Arial, sans-serif; font-size: 13.5px; font-weight: 500;
    display: flex; align-items: center; justify-content: center;
  }
  .footer-code { position: absolute; right: 53px; font-weight: 400; }
</style>
</head>
<body>
  <header class="site-header">
    <span class="brand-name">BRAMBLES</span>
  </header>

  <main class="hero">
    <div class="hero-photo" role="img" aria-label="Close-up photo of a chicken burger with lettuce, sauce and lemon on a wooden board"></div>

    <section class="intro-panel">
      <div class="intro-frame">
        <h1 class="intro-title">Brambles Cookbook</h1>
        <h2 class="intro-subtitle">Introduction</h2>
        <div class="intro-text">
          <p>Opening it’s doors in January of 2010, Brambles European Deli was a sandwich shop in Alderbrook, Nova Terra, but also a lot more than that.</p>
          <p>We spent five years with this business until it’s eventual closure in April of 2015. It was a special time where we met tons of amazing people, who we loved to see and serve.</p>
          <p>Brambles started out as a deli but eventually morphed into the sandwich shop we all know it as today.</p>
          <p>We are overwhelmed with the continuous positive messages and comments we<br>get on our Friendbook page that is still up and running.</p>
          <p>Unfortunately, we can’t open another Brambles, but we can offer you this<br>collection of our recipes for you to try out at home with your family and friends.</p>
          <p>If you do, please post your pictures of you making a meal or the finished product, or even enjoying it!</p>
        </div>
      </div>
    </section>

    <div class="offer-circle"></div>
    <div class="book-cover" role="img" aria-label="3D cover of the Brambles Sandwiches cookbook showing a sandwich on a plate"></div>

    <div class="price-block">
      <p class="price-label">Our Price</p>
      <p class="price-amount">$29.99</p>
    </div>
    <a class="buy-button" href="#buy">Buy Now</a>
  </main>

  <footer class="site-footer">
    <span>Copyright © 2022 | All Rights Reserved</span>
    <span class="footer-code">C44</span>
  </footer>
</body>
</html>
```